Dalvick's Business Card

I need some designs for a new business card including the new logo attached. An old example of our business card is also attached to show all the data that should be included on the new design.
**I added some more examples someone had mocked up**

Contact Information for Business Card

Should include all info on other examples uploaded.

```html
<!DOCTYPE html>
<html lang="en">
<head>
<meta charset="UTF-8">
<title>Dalvick's Business Card</title>
<link rel="stylesheet" href="https://fonts.googleapis.com/css2?family=Montserrat:wght@500;700;800&family=Poppins:wght@500;600&display=swap">
<style>
  :root {
    --stage: #2b2b2b;
    --card-dark: #1a1a1a;
    --card-light: #ffffff;
    --brand-blue: #0a6fc2;
    --brand-red: #e8202a;
    --ink: #1c1c1c;
    --muted-mark: #4a4a4a;
    --white: #ffffff;
  }
  html, body {
    margin: 0;
    width: 1200px;
    height: 1040px;
    overflow: hidden;
    background: var(--stage);
  }
  .stage {
    position: relative;
    width: 1200px;
    height: 1040px;
  }
  .card {
    position: absolute;
    left: 260px;
    width: 680px;
    height: 388px;
    border-radius: 0 64px 0 64px;
    overflow: hidden;
  }
  /* Back side */
  .card--back {
    top: 70px;
    background: var(--card-dark);
    color: var(--white);
    font-family: "Poppins", sans-serif;
    text-align: center;
  }
  .wordmark {
    display: flex;
    align-items: center;
    gap: 14px;
    font-family: "Montserrat", sans-serif;
    font-weight: 700;
    letter-spacing: 1px;
    white-space: nowrap;
  }
  .card--back .wordmark {
    position: absolute;
    top: 110px;
    left: 0;
    right: 0;
    justify-content: center;
    font-size: 58px;
    color: var(--muted-mark);
  }
  .wordmark__dot {
    width: 48px;
    height: 48px;
    border-radius: 50%;
    background: currentColor;
    flex: none;
  }
  .service-area {
    position: absolute;
    top: 250px;
    left: 0;
    right: 0;
    margin: 0;
    font-weight: 600;
    font-size: 19px;
    letter-spacing: 0.5px;
  }
  .divider {
    position: absolute;
    top: 286px;
    left: 50%;
    width: 100px;
    margin-left: -50px;
    border-top: 1px solid #777;
  }
  .call-to-action {
    position: absolute;
    top: 298px;
    left: 0;
    right: 0;
    margin: 0;
    font-weight: 600;
    font-size: 16px;
    letter-spacing: 0.6px;
    text-transform: uppercase;
  }
  /* Front side */
  .card--front {
    top: 540px;
    background: var(--card-light);
    font-family: "Montserrat", sans-serif;
  }
  .name-band {
    position: absolute;
    top: 62px;
    left: 0;
    width: 380px;
    height: 58px;
    background: var(--brand-blue);
    clip-path: polygon(0 0, 100% 0, 87% 100%, 0 100%);
    color: var(--white);
    font-weight: 800;
    font-size: 29px;
    line-height: 58px;
    padding-left: 62px;
    box-sizing: border-box;
    text-transform: uppercase;
  }
  .card--front .wordmark {
    position: absolute;
    top: 124px;
    right: 46px;
    font-size: 40px;
    gap: 12px;
    color: var(--brand-blue);
  }
  .card--front .wordmark__dot {
    width: 36px;
    height: 36px;
  }
  .contact {
    position: absolute;
    top: 222px;
    left: 56px;
    margin: 0;
    padding: 0;
    list-style: none;
    font-family: "Montserrat", sans-serif;
    font-weight: 500;
    font-size: 22px;
    color: var(--ink);
  }
  .contact li {
    display: flex;
    align-items: center;
    gap: 14px;
    margin-bottom: 6px;
  }
  .contact svg { width: 22px; height: 22px; flex: none; }
  .credentials {
    position: absolute;
    top: 298px;
    right: 58px;
    margin: 0;
    font-weight: 800;
    font-size: 22px;
    color: var(--brand-blue);
    text-transform: uppercase;
  }
  .family-band {
    position: absolute;
    right: 0;
    top: 332px;
    width: 460px;
    height: 50px;
    background: var(--brand-red);
    clip-path: polygon(7% 0, 100% 0, 100% 100%, 0 100%);
    color: var(--white);
    font-weight: 800;
    font-size: 23px;
    line-height: 50px;
    text-align: right;
    padding-right: 52px;
    box-sizing: border-box;
    text-transform: uppercase;
  }
</style>
</head>
<body>
<main class="stage">
  <section class="card card--back" aria-label="Card back">
    <div class="wordmark"><span class="wordmark__dot"></span>DALVICK'S</div>
    <p class="service-area">Serves Ridgefield, IA &amp; Surrounding Areas</p>
    <span class="divider"></span>
    <p class="call-to-action">Call today for all your HVAC, refrigeration &amp; plumbing needs</p>
  </section>

  <section class="card card--front" aria-label="Card front">
    <div class="name-band">Neil Dalvick</div>
    <div class="wordmark"><span class="wordmark__dot"></span>DALVICK'S</div>
    <ul class="contact">
      <li>
        <svg viewBox="0 0 24 24" aria-hidden="true"><path fill="#e8202a" d="M6.6 10.8a15.1 15.1 0 0 0 6.6 6.6l2.2-2.2c.3-.3.7-.4 1-.2 1.1.4 2.3.6 3.6.6.6 0 1 .4 1 1V20c0 .6-.4 1-1 1A17 17 0 0 1 3 4c0-.6.4-1 1-1h3.5c.6 0 1 .4 1 1 0 1.3.2 2.5.6 3.6.1.3 0 .7-.2 1z"/></svg>
        555.014.2290
      </li>
      <li>
        <svg viewBox="0 0 24 24" aria-hidden="true"><path fill="#e8202a" d="M2 5h20v14H2z"/><path fill="none" stroke="#fff" stroke-width="1.6" d="M2 5l10 8 10-8"/></svg>
        hvacdalvick@mailbox.com
      </li>
    </ul>
    <p class="credentials">Licensed &amp; Insured</p>
    <div class="family-band">Family Owned &amp; Operated</div>
  </section>
</main>
</body>
</html>
```